Tellmora Corporate Stationery

Look for design of all new corporate stationery for an existing insurance broking business that is going through a redesign and move from older partners to younger family members. New Logo is attached. Company is Brisbane based.
Colours in the Logo is Hex #43bed8 and website features a lot of hex #17b8d8. Website front page "A plan to protect you" - headline. "Professional and Individual advice to protect your greatest assets" - tagline.

Stationery required: Business Cards, Letter head, Thank-you cards, Birthday cards, Presentation folders, With Compliment slips and a powerpoint template. We also would like to send a card to all customers with the something along of the lines of "something new".

Target Market(s)

Customers of Insurance business looking at superannuation, life and income protection insurance, investment advice and wills

Industry/Entity Type

Insurance Broker

Font styles to use
Other font styles liked:
• same as logo

Requirements
Must have
• The above designs for new stationery for the new business including:
• Business Cards, Letter head, Thank-you cards, Birthday cards, Presentation folders, With Compliment slips and a powerpoint template. We also would like to send a card to all customers with the something along of the lines of "something new".
Nice to have
• It is a new look - long time family business being passed to next generation - big focus on advice for YOU, individual advice etc..

```html
<!DOCTYPE html>
<html lang="en">
<head>
<meta charset="utf-8">
<title>Tellmora Business Card</title>
<link href="https://fonts.googleapis.com/css2?family=Source+Sans+3:wght@400;600&display=swap" rel="stylesheet">
<style>
  :root {
    --backdrop: #e9e9e7;
    --card-white: #ffffff;
    --card-grey-dark: #9c9c9c;
    --card-grey-light: #d4d4d4;
    --teal: #43bed8;
    --ink-grey: #6e6e6e;
    --text-light: #ffffff;
  }
  * { margin: 0; padding: 0; box-sizing: border-box; }
  html, body {
    width: 1200px; height: 843px; overflow: hidden;
    background: var(--backdrop);
    font-family: "Source Sans 3", Arial, sans-serif;
  }
  .stage {
    position: relative; width: 1200px; height: 843px;
    display: flex; align-items: center; justify-content: center; gap: 60px;
  }
  .card {
    position: relative; width: 520px; height: 297px; overflow: hidden;
    box-shadow: 0 8px 24px rgba(0,0,0,0.18);
  }
  /* Front */
  .card-front { background: var(--card-white); }
  .brand {
    position: absolute; left: 0; right: 0; top: 112px;
    display: flex; align-items: center; justify-content: center; gap: 14px;
  }
  .brand-dot {
    width: 40px; height: 40px; border-radius: 50%; background: var(--teal);
  }
  .brand-name {
    font-weight: 600; font-size: 40px; letter-spacing: 3px;
    color: var(--teal); text-transform: uppercase;
  }
  .front-web {
    position: absolute; left: 0; right: 0; bottom: 42px; text-align: center;
    font-size: 14px; letter-spacing: 9px; color: var(--ink-grey);
  }
  /* Back */
  .card-back {
    background: linear-gradient(100deg, var(--card-grey-dark) 0%, var(--card-grey-light) 55%, #bdbdbd 100%);
    color: var(--text-light);
  }
  .accent-disc {
    position: absolute; left: 268px; top: 48px;
    width: 300px; height: 300px; border-radius: 50%;
    background: radial-gradient(circle at 40% 35%, #ffffff 60%, #ececec 100%);
    box-shadow: 0 0 0 3px rgba(255,255,255,0.6);
  }
  .holder { position: absolute; left: 30px; top: 24px; }
  .holder-name {
    font-weight: 600; font-size: 17px; letter-spacing: 1px;
    color: var(--teal); text-transform: uppercase; line-height: 1.1;
  }
  .holder-role { font-size: 13px; margin-top: 2px; }
  .contact { position: absolute; left: 30px; top: 98px; font-size: 13.5px; line-height: 17px; }
  .address { margin-left: 20px; margin-bottom: 2px; }
  .contact-list { list-style: none; }
  .contact-list li { display: flex; align-items: center; gap: 8px; height: 18px; }
  .contact-list svg { width: 12px; height: 12px; flex: none; }
</style>
</head>
<body>
<main class="stage">
  <section class="card card-front" aria-label="Business card front">
    <div class="brand">
      <span class="brand-dot"></span>
      <span class="brand-name">Tellmora</span>
    </div>
    <p class="front-web">www.tellmora.com</p>
  </section>

  <section class="card card-back" aria-label="Business card back">
    <div class="accent-disc"></div>
    <div class="holder">
      <p class="holder-name">Daniel Rowe</p>
      <p class="holder-role">CEO/Founder</p>
    </div>
    <div class="contact">
      <p class="address">214 Harbour Street<br>Brisbane, QLD 4000</p>
      <ul class="contact-list">
        <li>
          <svg viewBox="0 0 12 12"><path d="M2.5 1 L4.5 1 L5.2 3.6 L4 4.6 Q5 7 7.4 8 L8.4 6.8 L11 7.5 L11 9.5 Q11 11 9.5 11 Q1 10.5 1 2.5 Q1 1 2.5 1Z" fill="var(--teal)"/></svg>
          07 3041 5726
        </li>
        <li>
          <svg viewBox="0 0 12 12"><rect x="3" y="0.5" width="6" height="11" rx="1" fill="var(--teal)"/><rect x="4" y="2" width="4" height="6.5" fill="#c4c4c4"/></svg>
          0412 338 905
        </li>
        <li>
          <svg viewBox="0 0 12 12"><rect x="3" y="1" width="6" height="3" fill="var(--teal)"/><rect x="1" y="4.5" width="10" height="5" rx="1" fill="var(--teal)"/><rect x="3" y="8" width="6" height="3" fill="#e0e0e0"/></svg>
          07 3041 5727
        </li>
        <li>
          <svg viewBox="0 0 12 12"><rect x="0.5" y="2" width="11" height="8" rx="1" fill="var(--teal)"/><path d="M1 2.5 L6 6.5 L11 2.5" stroke="#c4c4c4" fill="none"/></svg>
          daniel@tellmora.com
        </li>
        <li>
          <svg viewBox="0 0 12 12"><circle cx="6" cy="6" r="5.5" fill="var(--teal)"/><path d="M0.5 6 H11.5 M6 0.5 Q2.5 6 6 11.5 M6 0.5 Q9.5 6 6 11.5" stroke="#c4c4c4" stroke-width="0.8" fill="none"/></svg>
          www.tellmora.com
        </li>
      </ul>
    </div>
  </section>
</main>
</body>
</html>
```